A new presentation to our clients

we are a Real Estate agency, our website is www.lumibrasa.com and it’s time to have a new, fashion and remarcable Business Card. we want to differentiate ourselves from other companies so we want a business card that differentiates us. we want the business card to impact our customers. in the competitive market that we have today, we have to be different and it is this difference that we seek

Target Market(s)

Real Estate Clients

Contact Information for Business Card

We search a totaly diferent card from the usual

Font styles to use
Sans Serif

Colors
e34197

Requirements
Must have
• Logo, adress, phone contact, e-mail, photo, and our website
Nice to have
• We would like to see a modern business card
Should not have
• Houses or building draws

```html
<!DOCTYPE html>
<html lang="en">
<head>
<meta charset="utf-8">
<title>Lumibrasa Business Card</title>
<link href="https://fonts.googleapis.com/css2?family=Roboto:wght@400;500;700&display=swap" rel="stylesheet">
<style>
  :root {
    --brand-pink: #e3197a;
    --card-white: #ffffff;
    --card-black: #000000;
    --text-grey: #4a4a4a;
    --backdrop: #d4d4d4;
  }
  * { margin: 0; padding: 0; box-sizing: border-box; }
  html, body {
    width: 1200px; height: 800px; overflow: hidden;
    background: var(--backdrop);
    font-family: "Roboto", Arial, sans-serif;
  }
  .stage {
    width: 1200px; height: 800px;
    display: flex; align-items: center; justify-content: center; gap: 40px;
  }
  .card {
    position: relative;
    width: 540px; height: 309px;
    box-shadow: 0 6px 18px rgba(0,0,0,0.18);
  }
  .card-back {
    background: var(--card-black);
    display: flex; align-items: center; justify-content: center;
  }
  .wordmark {
    color: var(--brand-pink);
    font-weight: 700;
    letter-spacing: 1px;
  }
  .card-back .wordmark { font-size: 64px; }
  .card-front { background: var(--card-white); }
  .card-front .wordmark {
    position: absolute; top: 40px; right: 40px;
    font-size: 38px;
  }
  .divider {
    position: absolute; left: 180px; right: 40px; top: 140px;
    height: 1.5px; background: var(--brand-pink);
  }
  .accent-square {
    position: absolute; left: 0; top: 128px;
    width: 22px; height: 38px; background: var(--brand-pink);
  }
  .person { position: absolute; left: 40px; top: 112px; }
  .person-name {
    color: var(--brand-pink); font-size: 20px; font-weight: 500;
    text-transform: uppercase; letter-spacing: 0.2px;
  }
  .person-role { color: var(--text-grey); font-size: 14px; margin-top: 2px; }
  .contact {
    position: absolute; left: 40px; bottom: 34px;
    list-style: none; color: var(--text-grey); font-size: 13px; line-height: 1.55;
  }
  .contact .label { color: var(--brand-pink); font-weight: 500; }
</style>
</head>
<body>
  <main class="stage">
    <section class="card card-back" aria-label="Card back">
      <span class="wordmark">Lumibrasa</span>
    </section>
    <section class="card card-front" aria-label="Card front">
      <span class="wordmark">Lumibrasa</span>
      <div class="accent-square"></div>
      <div class="person">
        <p class="person-name">Daniel Moreira</p>
        <p class="person-role">Director</p>
      </div>
      <div class="divider"></div>
      <ul class="contact">
        <li><span class="label">P</span> : (+351) 210 555 140 | <span class="label">F</span> : (+351) 210 555 149 | <span class="label">E</span> : geral@lumibrasa.com</li>
        <li><span class="label">W</span> : www.lumibrasa.com</li>
        <li><span class="label">A</span> : Av. da Liberdade, 210 4450-118, Matosinhos</li>
      </ul>
    </section>
  </main>
</body>
</html>
```